Tovimar Community Development Planning New web site

Design a new web site. I have a budget of $1,500.00.
Attached on PowerPoint is a complete site plan. Home page and linked pages.
10 - 12 pages. All copy and photos will be supplied. (300dpi)
I have shown them the concept which they like.
No data bases required. Home page with animations dissolving.
They former web site has been taken down. They have been in business 30 years in New Jersey
Colors teal blues and greens
There will be a new logo)being designed)
The text in home page copy will give you a detailed story what they are all about.

files have been approved for Tovimar, Inc.   Brenton is the designer

```html
<!DOCTYPE html>
<html lang="en">
<head>
<meta charset="utf-8">
<title>Tovimar, Inc. — Community Development Planning</title>
<link rel="stylesheet" href="https://fonts.googleapis.com/css2?family=Source+Sans+3:ital,wght@0,400;0,600;0,700;1,400&display=swap">
<style>
  :root {
    --white: #ffffff;
    --text: #5a5a5a;
    --heading: #666666;
    --rule: #d6d6d6;
    --dark: #263239;
    --card: #efefef;
    --card-text: #555555;
    --band: #f7f7f7;
    --badge: #c9c9c9;
    --footer-text: #c9cdd0;
    --photo-a: #b9cbdc;
    --photo-b: #4f6f99;
  }
  * { margin: 0; padding: 0; box-sizing: border-box; }
  html, body { width: 1200px; height: 982px; overflow: hidden; background: var(--white); }
  body { font-family: "Source Sans 3", "Source Sans Pro", sans-serif; color: var(--text); position: relative; }

  .section-title { position: absolute; left: 117px; font-weight: 700; }
  .section-rule { position: absolute; left: 117px; width: 38px; height: 1px; }

  /* Company */
  .company { position: absolute; left: 0; top: 0; width: 1200px; height: 476px; }
  .company .section-title { top: 44px; font-size: 23px; color: var(--heading); }
  .company .section-rule { top: 84px; background: var(--rule); }
  .company-copy { position: absolute; left: 117px; top: 111px; width: 418px; font-size: 12.6px; line-height: 15.8px; }
  .company-copy p + p { margin-top: 15.6px; }
  .company-photo { position: absolute; left: 614px; top: 99px; width: 511px; height: 290px;
    background: linear-gradient(160deg, var(--photo-a) 0%, #8ea9c4 45%, var(--photo-b) 100%); }

  /* Testimonials */
  .testimonials { position: absolute; left: 0; top: 476px; width: 1200px; height: 342px; background: var(--dark); }
  .testimonials .section-title { top: 47px; font-size: 19px; color: var(--white); }
  .testimonials .section-rule { top: 91px; background: #56636a; }
  .quote { position: absolute; top: 116px; width: 292px; }
  .quote-box { position: relative; height: 90px; background: var(--card); padding: 15px 19px 0; font-size: 13.2px; line-height: 20.6px; color: var(--card-text); }
  .quote-box::after { content: ""; position: absolute; right: 32px; bottom: -13px; border-top: 13px solid var(--card); border-left: 17px solid transparent; }
  .quote-author { margin-top: 32px; padding-right: 11px; text-align: right; color: var(--white); }
  .quote-name { font-size: 11.6px; font-weight: 700; letter-spacing: 0.2px; line-height: 15px; }
  .quote-role { font-size: 11px; font-style: italic; line-height: 14px; padding-right: 2px; }
  .read-more { position: absolute; right: 75px; top: 299px; font-size: 11.6px; color: var(--white); text-decoration: none; letter-spacing: 0.2px; }

  /* Memberships */
  .members { position: absolute; left: 0; top: 818px; width: 1200px; height: 94px; background: var(--band); }
  .members-label { position: absolute; left: 115px; top: 34px; font-size: 19px; font-weight: 700; color: var(--heading); }
  .badge { position: absolute; background: var(--badge); }

  /* Footer */
  .site-footer { position: absolute; left: 0; top: 912px; width: 1200px; height: 70px; background: var(--dark);
    font-size: 12.8px; color: var(--footer-text); text-align: center; line-height: 70px; }
</style>
</head>
<body>
  <section class="company">
    <h2 class="section-title">Our company</h2>
    <div class="section-rule"></div>
    <div class="company-copy">
      <p>Tovimar, Inc stands for Community, Grants, Planning and Housing. We specialize in all aspects of affordable housing, planning, COAH compliance, and the procurement of grants and loans for our clients.</p>
      <p>Founded in 1975, Tovimar has grown to be the only full service affordable housing implementation company in New Jersey. Seasoned in all facets of community development, Tovimar boasts a team that includes professional planners, expert grant-writers, COAH certified housing specialists, licensed building inspectors, lead testers, and knowledgeable support staff. Client needs are promptly met with continuity, efficiency and individual attention to detail.</p>
      <p>Tovimar serves as the Administrative Agent for more than 1,700 affordable homes and has also supervised the rehabilitation of more than 2,500 homes. Tovimar grant writing team secures more than $15 million each year for our clients. More than $250 million has been realized to date for Tovimar clients.</p>
    </div>
    <div class="company-photo" role="img" aria-label="Photo of a planning team in business attire and a hard hat reviewing building plans at a table"></div>
  </section>

  <section class="testimonials">
    <h2 class="section-title">Testimonials</h2>
    <div class="section-rule"></div>

    <figure class="quote" style="left:117px">
      <blockquote class="quote-box">Nullam quis risus eget urna mollis ornare vel eu leo. Maecenas faucibus mollis interdum. Nulla vitae elit libero, a pharetra augue.</blockquote>
      <figcaption class="quote-author"><div class="quote-name">JOHN MALCOLM DOE</div><div class="quote-role">Major of Dream City</div></figcaption>
    </figure>
    <figure class="quote" style="left:475px">
      <blockquote class="quote-box">Nullam quis risus eget urna mollis ornare vel eu leo. Maecenas faucibus mollis interdum. Nulla vitae elit libero, a pharetra augue.</blockquote>
      <figcaption class="quote-author"><div class="quote-name">JOHN MALCOLM DOE</div><div class="quote-role">Major of Dream City</div></figcaption>
    </figure>
    <figure class="quote" style="left:833px">
      <blockquote class="quote-box">Nullam quis risus eget urna mollis ornare vel eu leo. Maecenas faucibus mollis interdum. Nulla vitae elit libero, a pharetra augue.</blockquote>
      <figcaption class="quote-author"><div class="quote-name">JOHN MALCOLM DOE</div><div class="quote-role">Major of Dream City</div></figcaption>
    </figure>

    <a class="read-more" href="#">READ MORE</a>
  </section>

  <section class="members">
    <h3 class="members-label">Tovimar is a member of:</h3>
    <div class="badge" style="left:427px;top:35px;width:151px;height:22px" aria-label="Member association badge" role="img"></div>
    <div class="badge" style="left:660px;top:23px;width:47px;height:47px" aria-label="Member association badge" role="img"></div>
    <div class="badge" style="left:825px;top:20px;width:45px;height:54px;border-radius:50%" aria-label="Member association badge" role="img"></div>
    <div class="badge" style="left:950px;top:32px;width:175px;height:28px" aria-label="Member association badge" role="img"></div>
  </section>

  <footer class="site-footer">
    Copy Right 2014 Tovimar, 215 Harborview Lane, Seacrest, New Jersey, 08799&nbsp;&nbsp; TEL (555) 310-4482 Fax (555) 310-4490
  </footer>
</body>
</html>
```